Web Developer Needs a Business Card Design

I need a personal business card design that represents me as a web developer for potential employers. I would like the background to be a dark color on the front for contrast with my logo and name. The back will have all my information along with a smaller version of the logo. I want something with a modern look and feel, not too conservative. This will be used for potential employers and freelance work.

Industry/Entity Type

Business

Contact Information for Business Card

Front should have my logo and name. The back should have all my personal information which would include: name: Tom Varulek, phone: 570-614-3098, email: tomvarulek@quillbox.net, website url: www.tomvarulek.net, logo, web developer.

Font styles to use
Sans Serif

Requirements
Must have
• Must include my logo. The color palette base color will be the logo color.

```html
<!DOCTYPE html>
<html lang="en">
<head>
<meta charset="utf-8">
<title>Tom Varulek — Business Card</title>
<link rel="stylesheet" href="https://fonts.googleapis.com/css2?family=Source+Sans+3:wght@400;600;700&display=swap">
<style>
  :root {
    --page-bg: #2b2b2b;
    --card-bg: #1a1a1a;
    --accent: #6fd1b9;
    --text-light: #f2f2f2;
    --text-muted: #d6d6d6;
  }
  * { box-sizing: border-box; margin: 0; padding: 0; }
  html, body { width: 1200px; height: 900px; overflow: hidden; }
  body {
    background: var(--page-bg);
    font-family: "Source Sans 3", "Myriad Pro", Arial, sans-serif;
    position: relative;
  }
  .card {
    position: absolute;
    top: 300px;
    width: 525px;
    height: 300px;
    background: var(--card-bg);
    border-radius: 18px;
  }
  .card--back { left: 55px; }
  .card--front { left: 620px; }

  /* Brand mark: plain ring with the name */
  .brand {
    position: absolute;
    display: flex;
    flex-direction: column;
    align-items: center;
    gap: 10px;
  }
  .brand__ring {
    border: 6px solid var(--accent);
    border-radius: 50%;
  }
  .brand__name {
    color: var(--accent);
    font-weight: 600;
    letter-spacing: 0.02em;
  }
  .card--back .brand { left: 62px; top: 78px; width: 150px; }
  .card--back .brand__ring { width: 100px; height: 100px; }
  .card--back .brand__name { font-size: 20px; }

  .divider {
    position: absolute;
    left: 262px;
    top: 58px;
    width: 1.5px;
    height: 184px;
    background: linear-gradient(to bottom, transparent, var(--accent), transparent);
  }
  .contact {
    position: absolute;
    left: 290px;
    top: 72px;
  }
  .contact__name {
    color: var(--accent);
    font-size: 22px;
    font-weight: 600;
    line-height: 1.1;
  }
  .contact__role {
    color: var(--text-light);
    font-size: 14px;
    margin-top: 2px;
  }
  .contact__list {
    list-style: none;
    margin-top: 26px;
  }
  .contact__item {
    display: flex;
    align-items: center;
    gap: 9px;
    color: var(--text-light);
    font-size: 15px;
    line-height: 25px;
  }
  .contact__icon { width: 12px; height: 12px; fill: var(--accent); flex: none; }

  .card--front .brand { left: 0; right: 0; top: 42px; }
  .card--front .brand__ring { width: 116px; height: 116px; }
  .card--front .brand__name { font-size: 18px; }
  .front-name {
    position: absolute;
    left: 0; right: 0;
    top: 206px;
    text-align: center;
    color: var(--text-light);
    font-size: 24px;
    font-weight: 700;
    letter-spacing: 0.04em;
  }
  .front-role {
    position: absolute;
    left: 0; right: 0;
    top: 238px;
    text-align: center;
    color: var(--accent);
    font-size: 16px;
  }
</style>
</head>
<body>
  <section class="card card--back" aria-label="Card back">
    <div class="brand">
      <div class="brand__ring"></div>
      <span class="brand__name">Varulek</span>
    </div>
    <div class="divider"></div>
    <div class="contact">
      <p class="contact__name">Tom Varulek</p>
      <p class="contact__role">Front-End Developer</p>
      <ul class="contact__list">
        <li class="contact__item">
          <svg class="contact__icon" viewBox="0 0 24 24" aria-hidden="true"><path d="M6.6 10.8a15 15 0 0 0 6.6 6.6l2.2-2.2c.3-.3.7-.4 1-.2 1.1.4 2.3.6 3.6.6.6 0 1 .4 1 1V20c0 .6-.4 1-1 1A17 17 0 0 1 3 4c0-.6.4-1 1-1h3.5c.6 0 1 .4 1 1 0 1.3.2 2.5.6 3.6.1.3 0 .7-.2 1z"/></svg>
          570-614-3098
        </li>
        <li class="contact__item">
          <svg class="contact__icon" viewBox="0 0 24 24" aria-hidden="true"><path d="M2 5h20v14H2z M4 7v.5l8 5 8-5V7z" fill-rule="evenodd"/></svg>
          tomvarulek@quillbox.net
        </li>
        <li class="contact__item">
          <svg class="contact__icon" viewBox="0 0 24 24" aria-hidden="true"><path d="M10 14a4 4 0 0 1 0-5.7l3-3a4 4 0 0 1 5.7 5.7l-1.5 1.5-1.4-1.4 1.5-1.5a2 2 0 0 0-2.9-2.9l-3 3a2 2 0 0 0 0 2.9zM14 10a4 4 0 0 1 0 5.7l-3 3A4 4 0 0 1 5.3 13l1.5-1.5 1.4 1.4-1.5 1.5a2 2 0 0 0 2.9 2.9l3-3a2 2 0 0 0 0-2.9z"/></svg>
          www.tomvarulek.net
        </li>
      </ul>
    </div>
  </section>

  <section class="card card--front" aria-label="Card front">
    <div class="brand">
      <div class="brand__ring"></div>
      <span class="brand__name">Varulek</span>
    </div>
    <p class="front-name">TOM VARULEK</p>
    <p class="front-role">Front-End Developer</p>
  </section>
</body>
</html>
```